Design Startseite Kanzlei-Homepage
Zielgruppe
Wir sind eine Rechtsanwaltskanzlei in Kornbühl (Allgäu) und regional sowie überregional in verschiedenen Rechtsgebieten tätig. Unsere Zielgruppe sind sowohl private als auch gewerbliche Mandanten.
Aufgabenstellung
Die bestehende Gestaltung wirkt derzeit aus unserer Sicht überholt. Insbesondere soll das bislang dominierende Rot vollständig entfallen.
Stattdessen stellen wir uns ein modernes, hochwertiges Erscheinungsbild vor, primär in dunklen Farbtönen (Anthrazit/Schwarz) kombiniert mit Beige- bzw. warmen Naturtönen. Ziel ist eine klare visuelle Anlehnung an unsere Kanzleiräumlichkeiten (siehe Fotos).
Die Webseite soll insgesamt moderner, klarer und visuell anspruchsvoller wirken, ohne an Seriosität und Zugänglichkeit einzubüßen. Die Balance zwischen hochwertigem Erscheinungsbild und mandantenorientierter Nutzerführung steht für uns im Vordergrund.

```html
<!DOCTYPE html>
<html lang="de">
<head>
<meta charset="utf-8">
<title>Kanzlei am Lindenhof – Startseite</title>
<link href="https://fonts.googleapis.com/css2?family=Roboto+Condensed:wght@400;500;700&family=Open+Sans:ital,wght@0,400;0,600;1,400;1,600&display=swap" rel="stylesheet">
<style>
:root{
  --anthracite:#333231;
  --cream:#eee7da;
  --tile:#ede5d6;
  --tan:#b9a486;
  --text-dark:#2f2e2c;
  --white:#ffffff;
}
*{box-sizing:border-box;margin:0;padding:0}
html,body{width:1200px;height:3756px;overflow:hidden}
body{position:relative;background:var(--cream);font-family:"Open Sans",Arial,sans-serif;color:var(--text-dark)}
.abs{position:absolute}
.heading{font-family:"Roboto Condensed","Arial Narrow",sans-serif;font-weight:700;text-transform:uppercase;letter-spacing:.5px}
.btn{display:inline-block;background:var(--anthracite);color:var(--white);font-family:"Open Sans",Arial,sans-serif;font-weight:600;font-size:10px;text-transform:uppercase;padding:8px 14px;letter-spacing:.3px}
.brand{font-family:"Roboto Condensed","Arial Narrow",sans-serif;font-weight:500;text-transform:uppercase;color:var(--white);letter-spacing:.5px;white-space:nowrap}

/* hero */
.hero-band{left:0;top:0;width:1200px;height:376px;background:var(--anthracite)}
.hero-photo{left:134px;top:0;width:932px;height:526px;background:linear-gradient(180deg,#3c4352 0%,#6e6656 45%,#4a4236 70%,#25231f 100%)}
.nav-logo{left:160px;top:34px;font-size:29px}
.nav{left:616px;top:41px;display:flex;gap:28px;font-size:10px;color:var(--white);text-transform:uppercase;letter-spacing:.3px}
.slider-arrow{top:178px;color:var(--white);font-size:30px}
.hero-card{left:222px;top:152px;width:306px;height:172px;background:rgba(255,255,255,.72);padding:22px 36px}
.hero-card h2{font-size:22px;color:var(--text-dark);margin-bottom:6px}
.hero-card p{font-size:11px;line-height:16px;margin-bottom:14px}
.pager{left:1030px;top:490px;display:flex;gap:4px}
.pager span{width:4px;height:28px;background:var(--white)}

/* intro */
.intro{left:327px;top:449px;width:548px;height:369px;background:var(--tan);padding:44px 46px;color:var(--white);box-shadow:0 2px 6px rgba(0,0,0,.15)}
.intro h1{font-size:23px;line-height:27px;color:var(--text-dark);margin-bottom:22px}
.intro h1 span{color:var(--white)}
.intro p{font-size:10.5px;line-height:17px;margin-bottom:16px}
.intro a{color:var(--text-dark);text-decoration:underline}

/* fields */
.fields-dark{left:0;top:902px;width:634px;height:483px;background:var(--anthracite)}
.fields-tan{left:634px;top:902px;width:566px;height:483px;background:var(--tan)}
.tile{width:174px;height:115px;background:var(--tile);display:flex;flex-direction:column;align-items:center;justify-content:flex-end;padding-bottom:10px}
.tile.active{background:var(--tan)}
.tile .icon{width:54px;height:54px;margin-bottom:12px}
.tile span{font-family:"Roboto Condensed",sans-serif;font-weight:700;font-size:16px;color:var(--tan);text-transform:uppercase;letter-spacing:.5px}
.tile.active span{color:var(--white)}
.field-text{left:701px;top:1006px;width:430px;color:var(--white)}
.field-text h2{font-size:22px;line-height:26px;color:var(--text-dark);margin-bottom:28px}
.field-text h2 span{color:var(--white)}
.field-text p{font-size:10.5px;line-height:17px;margin-bottom:16px}

/* rooms */
.rooms{left:325px;top:1528px;width:550px;height:394px;background:var(--tan);box-shadow:0 2px 6px rgba(0,0,0,.15)}
.rooms h2{position:absolute;left:45px;top:60px;font-size:22px;line-height:27px;color:var(--text-dark)}
.rooms .copy{position:absolute;left:96px;top:164px;width:314px;color:var(--white);font-size:10.5px;line-height:17px}
.rooms .copy p{margin-bottom:16px}
.room-img{box-shadow:0 2px 6px rgba(0,0,0,.25)}

/* team */
.team-band{left:0;top:2092px;width:1200px;height:576px;background:var(--anthracite)}
.team-photo{left:70px;top:2028px;width:1056px;height:703px;background:linear-gradient(180deg,#9a9896 0%,#7e7c79 50%,#5f5d5a 100%)}
.consult{left:324px;top:2292px;width:551px;height:400px;background:rgba(238,231,218,.88);padding:60px 48px}
.consult .kicker{font-size:21px;color:var(--tan)}
.consult h2{font-size:21px;line-height:26px;color:var(--text-dark);margin-bottom:28px}
.consult .copy{margin-left:46px;width:340px;font-size:10.5px;line-height:17px}
.consult .copy p{margin-bottom:16px}

/* reviews */
.reviews-head{left:0;top:2796px;width:1200px;text-align:center}
.reviews-head .kicker{font-size:21px;color:var(--tan)}
.reviews-head h2{font-size:21px;color:var(--text-dark)}
.review{background:var(--anthracite);color:var(--white);padding:18px 18px;font-size:10.5px;line-height:14px;font-style:italic;box-shadow:0 2px 6px rgba(0,0,0,.2)}
.review .stars{display:flex;justify-content:center;gap:2px;margin-bottom:10px}
.review strong{font-weight:600}

/* map */
.map{left:0;top:3332px;width:1200px;height:347px;background:linear-gradient(135deg,#ece8e2 0%,#e4dfd6 60%,#ddd3c0 100%)}
.address{left:327px;top:3389px;width:172px;height:227px;background:var(--tan);padding:26px 15px;box-shadow:0 2px 6px rgba(0,0,0,.2)}
.address h3{font-size:21px;line-height:22px;color:var(--text-dark);margin-bottom:8px}
.address p{font-size:10px;line-height:13px;color:var(--white)}
.address .contact{margin-top:10px;display:flex;align-items:center;gap:4px}

/* footer */
.footer{left:0;top:3679px;width:1200px;height:77px;background:var(--anthracite)}
.footer .brand{position:absolute;left:324px;top:26px;font-size:21px}
.footer .legal{position:absolute;left:749px;top:33px;font-size:9px;font-weight:700;color:var(--white);text-transform:uppercase}
</style>
</head>
<body>

<div class="abs hero-band"></div>
<div class="abs hero-photo" role="img" aria-label="Abendaufnahme des Kanzleigebäudes an einer belebten Straße"></div>
<div class="abs brand nav-logo">Kanzlei am Lindenhof</div>
<nav class="abs nav"><span>Rechtsgebiete</span><span>Über die Kanzlei</span><span>Terminvereinbarung</span><span>Kontakt</span></nav>
<div class="abs slider-arrow" style="left:26px">&#10094;</div>
<div class="abs slider-arrow" style="left:1152px">&#10095;</div>
<div class="abs hero-card">
  <h2 class="heading">Hier eine Headline</h2>
  <p>Lorem ipsum dolor sit amet, consectetur adipiscing elit, sed do eiusmod tempor incididunt ut labore et dolore magna aliqua.</p>
  <span class="btn">» Link ipsum</span>
</div>
<div class="abs pager"><span></span><span></span><span></span><span></span></div>

<section class="abs intro">
  <h1 class="heading">Rechtsanwälte und Fachanwälte<br>in Kornbühl: <span>Kanzlei am Lindenhof</span></h1>
  <p>Die Mitglieder unseres Anwaltsteams - jeweils ergänzt um ein ansprechend eingerichtetes und funktional ausgestattetes Sekretariat - spezialisieren sich in unterschiedliche Fachrichtungen, sodass für Sie eine große Bandbreite in der mandantenorientierten Rechtsberatung sichergestellt ist. Das gilt insbesondere für unsere Schwerpunkte im <a>Verkehrsrecht</a> und <a>Strafrecht</a> sowie im <a>Arbeitsrecht</a>, <a>Erbrecht</a>, <a>Mietrecht</a>, <a>Baurecht</a> und <a>Familienrecht</a>.</p>
  <p>Auf die Mandatierung externer Anwälte kann durch die thematische Vielfalt und Spezialisierung unserer Juristen in den meisten Fällen verzichtet werden. Gleichzeitig gewährleistet unser engagiertes Kanzleiteam eine rechtliche Unterstützung ganz nach Ihren individuellen Interessen, stets auf dem neuesten Stand von Rechtsprechung und Praxis.</p>
</section>

<div class="abs fields-dark"></div>
<div class="abs fields-tan"></div>
<div class="abs tile" style="left:207px;top:959px"><svg class="icon" viewBox="0 0 54 54"><circle cx="27" cy="27" r="27" fill="#cfc4b2"/><circle cx="20" cy="19" r="4" fill="#8a8177"/><circle cx="34" cy="19" r="4" fill="#8a8177"/><rect x="16" y="25" width="8" height="16" rx="2" fill="#8a8177"/><rect x="30" y="25" width="8" height="16" rx="2" fill="#8a8177"/></svg><span>Familienrecht</span></div>
<div class="abs tile" style="left:395px;top:959px"><svg class="icon" viewBox="0 0 54 54"><circle cx="27" cy="27" r="27" fill="#cfc4b2"/><rect x="22" y="14" width="16" height="8" rx="2" transform="rotate(-40 30 18)" fill="#8a8177"/><rect x="15" y="26" width="4" height="16" transform="rotate(50 17 34)" fill="#8a8177"/><rect x="14" y="39" width="26" height="4" fill="#8a8177"/></svg><span>Arbeitsrecht</span></div>
<div class="abs tile" style="left:207px;top:1088px"><svg class="icon" viewBox="0 0 54 54"><circle cx="27" cy="27" r="27" fill="#cfc4b2"/><circle cx="19" cy="29" r="7" fill="none" stroke="#8a8177" stroke-width="4"/><circle cx="35" cy="29" r="7" fill="none" stroke="#8a8177" stroke-width="4"/><rect x="24" y="22" width="6" height="3" fill="#8a8177"/></svg><span>Strafrecht</span></div>
<div class="abs tile active" style="left:395px;top:1088px"><svg class="icon" viewBox="0 0 54 54"><circle cx="27" cy="27" r="27" fill="#f2ece1"/><rect x="26" y="13" width="2" height="26" fill="#8a8177"/><rect x="15" y="17" width="24" height="2" fill="#8a8177"/><path d="M12 30h10l-5-11z M32 30h10l-5-11z" fill="none" stroke="#8a8177" stroke-width="1.5"/><rect x="20" y="39" width="14" height="3" fill="#8a8177"/></svg><span>Erbrecht</span></div>
<div class="abs tile" style="left:207px;top:1216px"><svg class="icon" viewBox="0 0 54 54"><circle cx="27" cy="27" r="27" fill="#cfc4b2"/><rect x="25" y="12" width="4" height="30" fill="#8a8177"/><path d="M29 16h10l3 3-3 3H29z M25 24H15l-3 3 3 3h10z" fill="#8a8177"/></svg><span>Verkehrsrecht</span></div>
<div class="abs tile" style="left:395px;top:1216px"><svg class="icon" viewBox="0 0 54 54"><circle cx="27" cy="27" r="27" fill="#cfc4b2"/><path d="M17 27l10-9 10 9v10H17z" fill="#8a8177"/><rect x="25" y="30" width="4" height="7" fill="#cfc4b2"/></svg><span>Mietrecht</span></div>
<div class="abs field-text">
  <h2 class="heading">Rechtsgebiet:<br><span>Erbrecht</span></h2>
  <p>Das Erbrecht ist komplex und die Folgen eines Erbfalls weitreichend, da oft hohe Summen im Raum stehen. Es ergeben immer wieder neue Gerichtsentscheidungen - eine rechtlich fundierte und ganzheitliche Betrachtung ist daher unerlässlich.</p>
  <p>Wir beraten und vertreten (potenzielle) Erben und Erblasser vor und nach dem Erbfall in allen rechtlichen Fragen.</p>
  <span class="btn" style="margin-top:8px">» Zum Erbrecht</span>
</div>

<section class="abs rooms">
  <h2 class="heading">Lorem ipsum dolor<br>sit amet<br>consectetur</h2>
  <div class="copy">
    <p>Lorem ipsum dolor sit amet, consectetur adipiscing elit, sed Lorem ipsum dolor sit amet, consectetur adipiscing elit, sed do eiusmod tempor incididunt ut labore et dolore magna aliqua. Ut enim ad minim veniam, quis nostrud exercitation ullamco laboris nisi ut aliquip ex ea commodo consequat.</p>
    <p>Duis aute irure dolor in reprehenderit in voluptate velit esse cillum dolore eu fugiat nulla pariatur.</p>
    <span class="btn">» Zur Übersicht</span>
  </div>
</section>
<div class="abs room-img" style="left:605px;top:1496px;width:128px;height:170px;background:linear-gradient(90deg,#3a3530,#a8875e 50%,#3a3530)" role="img" aria-label="Flur der Kanzlei mit Holzverkleidung"></div>
<div class="abs room-img" style="left:746px;top:1449px;width:174px;height:130px;background:linear-gradient(180deg,#bdb6ac,#6a6157 60%,#3e3934)" role="img" aria-label="Wartebereich mit dunklen Sesseln"></div>
<div class="abs room-img" style="left:746px;top:1589px;width:174px;height:130px;background:linear-gradient(180deg,#c9c3ba,#7d6b55 60%,#3a3631)" role="img" aria-label="Empfangstresen der Kanzlei"></div>

<div class="abs team-band"></div>
<div class="abs team-photo" role="img" aria-label="Gruppenfoto des Kanzleiteams auf einem gepflasterten Platz"></div>
<section class="abs consult">
  <div class="heading kicker">Persönliche Beratung</div>
  <h2 class="heading">Wir laden Sie zu einem kostenlosen<br>Gespräch ein</h2>
  <div class="copy">
    <p>Lorem ipsum dolor sit amet, consectetur adipiscing elit, sed Lorem ipsum dolor sit amet, consectetur adipiscing elit, sed do eiusmod tempor incididunt ut labore et dolore magna aliqua. Ut enim ad minim veniam, quis nostrud exercitation ullamco laboris nisi ut aliquip ex ea commodo consequat.</p>
    <p>Duis aute irure dolor in reprehenderit in voluptate velit esse cillum dolore eu fugiat nulla pariatur.</p>
    <span class="btn">» Zur Terminvereinbarung</span>
  </div>
</section>

<div class="abs reviews-head">
  <div class="heading kicker">Unsere Mandaten</div>
  <h2 class="heading">Ihre Meinung ist uns wichtig</h2>
</div>
<svg width="0" height="0" style="position:absolute"><defs><path id="star" d="M7 0l2 4.6 5 .5-3.8 3.3 1.1 4.9L7 10.8 2.7 13.3l1.1-4.9L0 5.1l5-.5z" fill="#b9a486"/></defs></svg>
<div class="abs review" style="left:325px;top:2906px;width:174px;height:244px">
  <div class="stars"><svg width="14" height="14"><use href="#star"/></svg><svg width="14" height="14"><use href="#star"/></svg><svg width="14" height="14"><use href="#star"/></svg><svg width="14" height="14"><use href="#star"/></svg><svg width="14" height="14"><use href="#star"/></svg></div>
  <strong>Absolute Empfehlung</strong><br>Herr Brenning hat mir geholfen, einen Streit mit meinem ehemaligen Arbeitgeber zu gewinnen. Dabei hat er es geschafft mir die Ruhe zu geben, die Auseinandersetzung durchzuhalten. Vielen Dank Herr Brenning, auch wenn ich nicht hoffe das es nochmal notwendig ist, immer wieder gerne bei Ihnen.
</div>
<div class="abs review" style="left:513px;top:2881px;width:174px;height:340px">
  <div class="stars"><svg width="14" height="14"><use href="#star"/></svg><svg width="14" height="14"><use href="#star"/></svg><svg width="14" height="14"><use href="#star"/></svg><svg width="14" height="14"><use href="#star"/></svg><svg width="14" height="14"><use href="#star"/></svg></div>
  <strong>Absolute Profis - Kanzlei am Lindenhof in Kornbühl</strong><br>Großes Lob an Herrn Ostwald und sein Team. Einfach eine erstklassige Beratung und hochkompetente Betreuung. Meine Anliegen wurden immer sofort bearbeitet und meine Fragen schnellstmöglich beantwortet. Darüber hinaus, in allen Fällen in denen mich Herr Ostwald vertreten hat, wurde ein erfolgreiches Ergebnis erzielt.<br><br>Diesbezüglich kann ich die Kanzlei am Lindenhof nur weiterempfehlen.
</div>
<div class="abs review" style="left:704px;top:2906px;width:174px;height:280px">
  <div class="stars"><svg width="14" height="14"><use href="#star"/></svg><svg width="14" height="14"><use href="#star"/></svg><svg width="14" height="14"><use href="#star"/></svg><svg width="14" height="14"><use href="#star"/></svg><svg width="14" height="14"><use href="#star"/></svg></div>
  <strong>Familienrecht</strong><br>Ich möchte mich hiermit bei dem ganzen Team der Kanzlei am Lindenhof für die sehr freundliche, zuvorkommende und vor allem faire Beratung und Bearbeitung in meinem Fall bedanken, die dann auch in meinem Sinne zum Erfolg führte. Gerne komme ich in zukünftigen Rechtsangelegenheiten wieder auf diese Kanzlei zurück.
</div>

<div class="abs map" role="img" aria-label="Stadtplan mit Standort der Kanzlei"></div>
<div class="abs address">
  <h3 class="heading">Kanzlei am<br>Lindenhof</h3>
  <p>Lindenweg 14<br>87399 Kornbühl</p>
  <p class="contact"><svg width="9" height="9" viewBox="0 0 10 10"><path d="M2 1l2 2-1 1.5c.7 1.3 1.2 1.8 2.5 2.5L7 6l2 2-1.5 1.5C4 9 1 6 .5 2.5z" fill="#fff"/></svg>0831 - 555 204 70</p>
  <p class="contact" style="margin-top:0"><svg width="9" height="9" viewBox="0 0 10 10"><rect x="0" y="2" width="10" height="7" fill="#fff"/><path d="M0 2l5 4 5-4" stroke="#b9a486" fill="none"/></svg>info@kanzlei-lindenhof.de</p>
  <span class="btn" style="margin-top:20px;width:142px">» Zur Anfahrt</span>
</div>
<svg class="abs" style="left:598px;top:3475px" width="14" height="20" viewBox="0 0 14 20"><path d="M7 0a7 7 0 0 1 7 7c0 5-7 13-7 13S0 12 0 7a7 7 0 0 1 7-7z" fill="#c08a3e"/><circle cx="7" cy="7" r="2.5" fill="#fff"/></svg>

<footer class="abs footer">
  <div class="brand">Kanzlei am Lindenhof</div>
  <div class="legal">Impressum | Datenschutz</div>
</footer>

</body>
</html>
```